VELMOR Website Design

We need a website designed for our company VELMOR. We are a luxury lifestyle club that will provide benefits and services for our members. The site should be clean & sleek, preferably using black and white (or darker colors). (example sites: stravenhall.example, plinth.example)

Here is a link of a sample page I did using wix. (https://dunmere7.sitehostly.example/mysite) This can be used to get a general idea.

Target Market(s)

Upper Middle Class in the United States

Number of Pages Required

5+ page

Font styles to use
Sans Serif
Other font styles liked:
• Arial (or other similar fonts)

Requirements
Must have
• A clean design that is eye-catching and speaks to our company.
Nice to have
• Ideas for copy.

```html
<!DOCTYPE html>
<html lang="en">
<head>
<meta charset="utf-8">
<title>VELMOR — A Members Only Lifestyle Club</title>
<link rel="stylesheet" href="https://fonts.googleapis.com/css2?family=Arimo:ital,wght@0,400;0,700;1,400&display=swap">
<style>
:root{
  --ink:#111111;
  --text:#333333;
  --muted:#555555;
  --paper:#ffffff;
  --mist:#f5f5f5;
  --line:#222222;
  --hero-a:#2a1d1a;
  --hero-b:#5a4034;
  --hero-c:#1a1418;
}
*{box-sizing:border-box;margin:0;padding:0}
html,body{width:1200px;height:3727px;overflow:hidden}
body{font-family:"Arimo",Arial,sans-serif;color:var(--text);background:var(--paper);position:relative}
.abs{position:absolute}
.center{left:0;width:1200px;text-align:center}
section,.footer{position:absolute;left:0;width:1200px}

/* hero */
.hero{top:0;height:641px;overflow:hidden}
.hero-photo{position:absolute;inset:0;background:
  radial-gradient(ellipse at 30% 70%,rgba(150,90,55,.55),transparent 55%),
  radial-gradient(ellipse at 70% 40%,rgba(120,70,50,.5),transparent 50%),
  linear-gradient(160deg,var(--hero-c),var(--hero-b) 50%,var(--hero-a));}
.hero-shade{position:absolute;inset:0;background:rgba(0,0,0,.28)}
.lang{top:8px;left:118px;color:#fff;font-size:12px;display:flex;align-items:center;gap:6px}
.login{top:8px;right:118px;color:#fff;font-size:12px;display:flex;align-items:center;gap:6px}
.brand{top:14px;color:#fff;font-size:40px;font-weight:700;letter-spacing:1px}
.main-nav{top:74px;display:flex;justify-content:center;gap:22px;color:#fff;font-size:13px}
.hero-title{top:282px;color:#fff;font-size:44px;font-weight:700}
.hero-sub{top:333px;color:#fff;font-size:13px}
.btn{position:absolute;height:45px;width:164px;border:2px solid var(--ink);background:var(--paper);color:var(--ink);font-size:13px;display:flex;align-items:center;justify-content:center}
.btn-ghost{border-color:#fff;background:transparent;color:#fff;left:527px;top:373px}
.hero-dots{top:584px;display:flex;justify-content:center;gap:10px}
.hero-dots span{width:12px;height:12px;border-radius:50%;background:#fff}
.hero-dots span.active{background:transparent;border:2px solid #fff}

h2{position:absolute;left:0;width:1200px;text-align:center;font-size:30px;font-weight:700;color:var(--ink);letter-spacing:.5px}
.rule{position:absolute;left:555px;width:90px;height:2px;background:var(--ink)}
.dots{position:absolute;left:0;width:1200px;display:flex;justify-content:center;gap:5px}
.dots span{width:6px;height:6px;border-radius:50%;background:var(--ink)}

/* about */
.about{top:641px;height:293px;background:var(--mist)}
.about p{position:absolute;left:149px;width:902px;top:110px;font-size:12.5px;line-height:20.5px;text-align:center;color:var(--muted)}

/* services */
.services{top:934px;height:1078px}
.kicker{top:150px;font-size:20px;font-weight:700;color:var(--ink)}
.intro{top:177px;font-size:12.5px;line-height:22px;color:var(--muted)}
.service{position:absolute;width:300px;text-align:center}
.service .photo{width:214px;height:214px;border-radius:50%;margin:0 auto}
.service h3{margin-top:30px;font-size:19px;font-weight:700;color:var(--ink)}

/* newsletter */
.newsletter{top:2012px;height:745px;background:var(--mist)}
.post{position:absolute;top:166px;width:313px}
.post .photo{height:232px}
.post .cat{margin-top:20px;font-size:13px;color:var(--muted)}
.post h3{margin-top:18px;font-size:13px;font-weight:700;color:var(--ink);line-height:17px;text-transform:uppercase}
.post p{margin-top:13px;font-size:12.5px;line-height:17.5px;color:var(--muted);text-align:justify}
.post .dots{position:static;width:auto;justify-content:flex-start;margin-top:14px}

/* contact */
.contact{top:2757px;height:477px}
.field{position:absolute;border-bottom:2px solid var(--line);height:26px;font-size:13px;font-style:italic;color:var(--text)}

/* subscribe */
.subscribe{top:3234px;height:219px;background:var(--mist)}
.subscribe h4{position:absolute;left:0;width:1200px;top:50px;text-align:center;font-size:18px;font-weight:700;color:var(--ink);line-height:24px;text-transform:uppercase}
.email{position:absolute;left:363px;top:124px;width:335px;height:45px;border:2px solid var(--line);background:#fff;font-size:13px;font-style:italic;padding:13px 16px;color:var(--muted)}
.send{position:absolute;left:703px;top:124px;width:134px;height:45px;background:var(--ink);color:#fff;font-size:13px;display:flex;align-items:center;justify-content:center}

/* footer */
.footer{top:3453px;height:274px}
.footer .brand{color:var(--ink);top:40px}
.foot-nav{top:103px;display:flex;justify-content:center;gap:22px;font-size:13px;color:var(--ink)}
.social{top:152px;display:flex;justify-content:center;gap:26px}
.social span{width:16px;height:16px;border-radius:50%;background:var(--ink)}
.foot-rule{position:absolute;left:122px;width:959px;top:206px;height:1px;background:#999}
.copy{top:230px;font-size:12px;color:var(--ink)}
</style>
</head>
<body>

<section class="hero">
  <div class="hero-photo" role="img" aria-label="Friends raising glasses of beer and wine in a toast"></div>
  <div class="hero-shade"></div>
  <div class="abs lang"><svg width="12" height="12" viewBox="0 0 12 12"><circle cx="6" cy="6" r="5.5" fill="#fff"/></svg>EN</div>
  <div class="abs login"><svg width="12" height="12" viewBox="0 0 12 12"><path d="M2 10 L10 2 M4 2 H10 V8" stroke="#fff" stroke-width="1.6" fill="none"/></svg>Login</div>
  <div class="abs center brand">VELMOR</div>
  <nav class="abs center main-nav"><span>Home</span><span>About</span><span>Services &amp; Benefits</span><span>Noted</span><span>Contact</span></nav>
  <div class="abs center hero-title">A MEMBERS ONLY LIFESTYLE CLUB</div>
  <div class="abs center hero-sub">Lorem Ipsum is simply dummy text of the printing and typesetting industry.</div>
  <div class="btn btn-ghost">Learn More</div>
  <div class="abs center hero-dots"><span class="active"></span><span></span><span></span></div>
</section>

<section class="about">
  <h2 style="top:48px">ABOUT US</h2>
  <p>Lorem Ipsum is simply dummy text of the printing and typesetting industry. Lorem Ipsum has been the industry's standard dummy text ever since the 1500s, when an unknown printer took a galley of type and scrambled it to make a type specimen book. It has survived not only five centuries, but also the leap into electronic typesetting, remaining essentially unchanged. It was popularised in the 1960s with the release of Quillset sheets containing Lorem Ipsum passages, and more recently with desktop publishing software like Halden PageSet including versions of Lorem Ipsum.</p>
  <div class="dots" style="top:235px"><span></span><span></span><span></span></div>
</section>

<section class="services">
  <h2 style="top:45px">SERVICES &amp; BENIFTS</h2>
  <div class="abs center kicker">WE ARE VELMOR</div>
  <div class="abs center intro">Built in the image of a"Multi-Family Office", VELMOR provides members with access to just about any service, experience, and event desirable.<br>VELMOR is truly the most exclusive lifestyle club out there.</div>
  <div class="btn" style="left:517px;top:236px">Apply For Membership</div>

  <div class="service" style="left:153px;top:333px"><div class="photo" role="img" aria-label="Hand using a calculator over paperwork" style="background:radial-gradient(circle at 40% 40%,#e8e4df,#9a9590 70%,#4a4a50)"></div><h3>ACCOUNTING SERVICES</h3></div>
  <div class="service" style="left:446px;top:333px"><div class="photo" role="img" aria-label="Blue stock market data screen" style="background:radial-gradient(circle at 50% 40%,#5a7fc0,#1f3a78 70%,#0e1c44)"></div><h3>INVESTMENT SERVICES</h3></div>
  <div class="service" style="left:739px;top:333px"><div class="photo" role="img" aria-label="Judge's gavel beside a hand signing documents" style="background:radial-gradient(circle at 50% 40%,#efece8,#b8a89a 70%,#6a4e3a)"></div><h3>LAWYER SERVICES</h3></div>

  <div class="service" style="left:153px;top:638px"><div class="photo" role="img" aria-label="Modern apartment building among trees" style="background:linear-gradient(180deg,#dfe6ee,#b7a98e 60%,#6f7a4e)"></div><h3>REAL ESTATE SERVICES</h3></div>
  <div class="service" style="left:446px;top:638px"><div class="photo" role="img" aria-label="Brass service bell on a hotel counter" style="background:radial-gradient(circle at 50% 55%,#d9a35a,#7a4a24 60%,#2a1a12)"></div><h3>24/7 CONCIERGE</h3></div>
  <div class="service" style="left:739px;top:638px"><div class="photo" role="img" aria-label="Black car parked beside a private jet" style="background:linear-gradient(180deg,#eef0f2,#c9ccd0 55%,#3a3c40)"></div><h3>PRIVATE JET TRAVEL</h3></div>

  <div class="btn" style="left:519px;top:976px">View All Services</div>
</section>

<section class="newsletter">
  <h2 style="top:52px">NEWSLETTER</h2>
  <div class="rule" style="top:107px"></div>

  <article class="post" style="left:122px">
    <div class="photo" role="img" aria-label="Couple with luggage watching a plane from an airport window" style="background:linear-gradient(180deg,#cfe0ee,#9fb4c6 60%,#5e6670)"></div>
    <div class="cat">Lifestyle, Travel</div>
    <h3>How Ashcombe Club's revamp<br>has elevated the golfing lifestyle</h3>
    <p>Lorem Ipsum is simply dummy text of the printing and typesetting industry. Lorem Ipsum has been the industry's standard dummy text ever since the 1500s.</p>
    <div class="dots"><span></span><span></span><span></span></div>
  </article>
  <article class="post" style="left:445px">
    <div class="photo" role="img" aria-label="Aerial view of a sandy spit between turquoise lagoon and sea" style="background:linear-gradient(160deg,#3aa7b8,#7fd0cf 45%,#d9c9a0 55%,#2e7fa0)"></div>
    <div class="cat">Travel</div>
    <h3>A heavenly experience on Turkey</h3>
    <p>Lorem Ipsum is simply dummy text of the printing and typesetting industry. Lorem Ipsum has been the industry's standard dummy text ever since the 1500s.</p>
    <div class="dots"><span></span><span></span><span></span></div>
  </article>
  <article class="post" style="left:768px">
    <div class="photo" role="img" aria-label="Banquet hall lit in purple and magenta for a private event" style="background:radial-gradient(ellipse at 50% 60%,#c43ad0,#6a1f8a 55%,#1a0a2a)"></div>
    <div class="cat">Events</div>
    <h3>Decoration for private events</h3>
    <p>Lorem Ipsum is simply dummy text of the printing and typesetting industry. Lorem Ipsum has been the industry's standard dummy text ever since the 1500s.</p>
    <div class="dots"><span></span><span></span><span></span></div>
  </article>

  <div class="btn" style="left:519px;top:636px">View More</div>
</section>

<section class="contact">
  <h2 style="top:80px">CONTACT US</h2>
  <div class="rule" style="top:137px"></div>
  <div class="field" style="left:271px;top:198px;width:203px">Name</div>
  <div class="field" style="left:497px;top:198px;width:206px">Email Address</div>
  <div class="field" style="left:725px;top:198px;width:206px">Phone Number</div>
  <div class="field" style="left:271px;top:270px;width:660px">Massage</div>
  <div class="btn" style="left:519px;top:351px">Submit</div>
</section>

<section class="subscribe">
  <h4>Subscribe to the latest news and experiences in<br>global luxury, contemporary culture, and exclusive offers</h4>
  <div class="email">Email Address</div>
  <div class="send">Send</div>
</section>

<footer class="footer">
  <div class="abs center brand">VELMOR</div>
  <nav class="abs center foot-nav"><span>Home</span><span>About</span><span>Services &amp; Benefits</span><span>Noted</span><span>Contact</span></nav>
  <div class="abs center social" aria-label="Social links"><span></span><span></span><span></span><span></span><span></span></div>
  <div class="foot-rule"></div>
  <div class="abs center copy">© Copyright 2018 VELMOR. All Right Reserved</div>
</footer>

</body>
</html>
```